2018 Desk Calendar Design with Better Spine, Better Health with Chiropractic

In conjunction with the Federation of Spinal Wellness Malaysia (FSW), we are organizing a 2018 desk calendar design. The cover page and monthly design size is 210mm (H) x 195mm (W). The will be a total of 27 designs including a cover page (front) [Sample 1], cover page (back) Malaysia National & States Holiday 2018 (https://restdaylist.example.my/2018-dates/) [Sample 2], 12 months design (front) [Sample 3 and 4], 12 months design (back) [Sample 5], Last page (2017 and 2019 calendar) [Sample 6].

Below are some recommendations for monthly back cover design. The main theme remain as Better SPINE, Better HEALTH with CHIROPRACTIC. Each month can in collaborate with of the following element:-

Suggestion 1 (Celebration of the Month)
January - New Year
February - Chinese New Year
March -
April -
May - Labour Day
June - Aidilfitri Festival
July-
August - Independent Day
September - Malaysia Day
October - World Spine Day
November - Deepavali Festival
December - Christmas

Suggestion 2 (States in Malaysia)
January - Perlis
February - Kedah
March - Penang
April - Perak
May - Selangor
June - Negeri Sembilan
July- Melaka
August - Johor
September - Pahang
October - Terengganu
November - Kelantan
December - Sabah & Sarawak

Target Market(s)

Chiropractors and Public

Industry/Entity Type

Chiropractor

Colors

Designer to choose colors to be used in the design.

Requirements
Must have
• The theme for the desk calendar design is Better Spine, Better Health with Chiropractic.
• The cover page should include 5th Anniversary element.
Nice to have
• Lunar or Islamic calendar is optional in the Gregorian calendar.
• AI Format
• Footnote of each page www.spinefsw.example.org

```html
<!DOCTYPE html>
<html lang="en">
<head>
<meta charset="utf-8">
<title>September 2018 – FSW Desk Calendar</title>
<link rel="stylesheet" href="https://fonts.googleapis.com/css2?family=Orbitron:wght@700;800&family=Michroma&family=Old+Standard+TT&family=Roboto:wght@400&display=swap">
<style>
  :root {
    --paper: #c8b9b6;
    --maroon: #6b0f17;
    --title-red: #7c1119;
    --sunday: #e3222b;
    --rule: #b3262a;
    --ink: #111111;
    --badge-blue: #243a8c;
    --band-pink: #e2948a;
    --band-orange: #ef7a52;
    --band-red: #c4452f;
    --band-shadow: #7e4f4c;
  }
  html, body { margin: 0; padding: 0; overflow: hidden; background: var(--paper); }
  .page {
    position: relative;
    width: 1115px;
    height: 1200px;
    background: var(--paper);
    overflow: hidden;
    font-family: "Orbitron", sans-serif;
  }
  .page-art { position: absolute; inset: 0; }

  .spine-fact {
    position: absolute;
    left: 30px;
    top: 220px;
    margin: 0;
    font-family: "Old Standard TT", serif;
    font-size: 30px;
    line-height: 39px;
    letter-spacing: 3px;
    color: transparent;
    -webkit-text-stroke: 1px #ffffff;
  }

  .mini-month { position: absolute; left: 852px; top: 306px; width: 250px; }
  .mini-month__title {
    margin: 0 0 6px 63px;
    font-family: "Michroma", sans-serif;
    font-size: 17px;
    letter-spacing: 2px;
    color: var(--ink);
  }
  .mini-month__grid {
    display: grid;
    grid-template-columns: repeat(7, 37px);
    row-gap: 12px;
    font-size: 15px;
    font-weight: 800;
    color: var(--ink);
  }
  .mini-month__grid .sun { color: var(--sunday); }

  .month-title {
    position: absolute;
    left: 504px;
    top: 524px;
    margin: 0;
    font-family: "Michroma", sans-serif;
    font-weight: 400;
    font-size: 58px;
    letter-spacing: 3px;
    color: var(--title-red);
    line-height: 1;
  }

  .anniversary {
    position: absolute;
    left: 348px;
    top: 508px;
    width: 112px;
    height: 86px;
    display: flex;
    align-items: center;
    gap: 8px;
    font-family: "Orbitron", sans-serif;
    font-weight: 700;
    font-size: 20px;
    color: var(--badge-blue);
  }
  .anniversary__dot {
    width: 34px; height: 34px; border-radius: 50%;
    border: 2px solid var(--badge-blue);
  }

  .month-grid { position: absolute; left: 0; top: 0; width: 1115px; height: 1200px; }
  .weekday, .day {
    position: absolute;
    font-weight: 800;
    color: var(--ink);
  }
  .weekday { font-size: 26px; top: 622px; }
  .day { font-size: 33px; }
  .sun { color: var(--sunday); }
  .week-rule {
    position: absolute;
    left: 134px;
    width: 910px;
    height: 2px;
    background: var(--rule);
  }

  .site-url {
    position: absolute;
    right: 20px;
    top: 1160px;
    font-family: "Roboto", sans-serif;
    font-size: 19px;
    color: var(--ink);
  }
</style>
</head>
<body>
<div class="page">

  <svg class="page-art" width="1115" height="1200" viewBox="0 0 1115 1200">
    <defs>
      <linearGradient id="gymTone" x1="0" y1="0" x2="1" y2="1">
        <stop offset="0" stop-color="#9fc2da"/>
        <stop offset="0.45" stop-color="#e9e1dc"/>
        <stop offset="0.75" stop-color="#d98a8a"/>
        <stop offset="1" stop-color="#b9cddc"/>
      </linearGradient>
    </defs>
    <path class="photo-area" role="img" aria-label="Photo of a smiling woman and her trainer lifting a barbell in a gym"
          d="M0,0 H1115 V40 C950,230 700,350 450,410 C250,460 100,520 0,640 Z" fill="url(#gymTone)"/>
    <g class="spine-curve" fill="none" stroke-linecap="butt">
      <path d="M-10,720 C100,530 250,480 450,430 C700,370 950,260 1125,70" stroke="var(--band-pink)" stroke-width="80"/>
      <path d="M-10,730 C100,540 250,490 450,440 C700,380 950,270 1125,80" stroke="var(--band-orange)" stroke-width="50"/>
      <path d="M-10,745 C100,555 250,505 450,455 C700,395 950,285 1125,95" stroke="var(--band-shadow)" stroke-width="14"/>
      <path d="M-10,735 C100,545 250,495 450,445 C700,385 950,275 1125,85" stroke="var(--band-red)" stroke-width="18"/>
    </g>
    <path role="img" aria-label="Row of stylised vertebrae forming a spine along the curve"
          d="M30,680 C110,520 260,470 450,420 C700,360 940,250 1115,40"
          fill="none" stroke="var(--maroon)" stroke-width="58"/>
  </svg>

  <p class="spine-fact">Spine Fact:<br>Human shrink somewhere between<br>a quarter and a third of an<br>inch each decade, after<br>the age of 40</p>

  <div class="mini-month">
    <p class="mini-month__title">AUGUST</p>
    <div class="mini-month__grid">
      <span>M</span><span>T</span><span>W</span><span>T</span><span>F</span><span>S</span><span class="sun">S</span>
      <span></span><span></span><span>1</span><span>2</span><span>3</span><span>4</span><span class="sun">5</span>
      <span>6</span><span>7</span><span>8</span><span>9</span><span>10</span><span>11</span><span class="sun">12</span>
      <span>13</span><span>14</span><span>15</span><span>16</span><span>17</span><span>18</span><span class="sun">19</span>
      <span>20</span><span>21</span><span>22</span><span>23</span><span>24</span><span>25</span><span class="sun">26</span>
      <span>27</span><span>28</span><span>29</span><span>30</span><span>31</span>
    </div>
  </div>

  <div class="anniversary"><span class="anniversary__dot"></span>FSW</div>

  <h1 class="month-title">SEPTEMBER</h1>

  <div class="month-grid">
    <span class="weekday" style="left:153px">M</span>
    <span class="weekday" style="left:274px">T</span>
    <span class="weekday" style="left:404px">W</span>
    <span class="weekday" style="left:534px">T</span>
    <span class="weekday" style="left:665px">F</span>
    <span class="weekday" style="left:792px">S</span>
    <span class="weekday sun" style="left:922px">S</span>

    <span class="day" style="left:792px;top:735px">1</span>
    <span class="day sun" style="left:922px;top:735px">2</span>
    <div class="week-rule" style="top:774px"></div>

    <span class="day" style="left:153px;top:830px">3</span>
    <span class="day" style="left:274px;top:830px">4</span>
    <span class="day" style="left:404px;top:830px">5</span>
    <span class="day" style="left:534px;top:830px">6</span>
    <span class="day" style="left:665px;top:830px">7</span>
    <span class="day" style="left:792px;top:830px">8</span>
    <span class="day sun" style="left:922px;top:830px">9</span>
    <div class="week-rule" style="top:868px"></div>

    <span class="day" style="left:153px;top:924px">10</span>
    <span class="day" style="left:274px;top:924px">11</span>
    <span class="day" style="left:404px;top:924px">12</span>
    <span class="day" style="left:534px;top:924px">13</span>
    <span class="day" style="left:665px;top:924px">14</span>
    <span class="day" style="left:792px;top:924px">15</span>
    <span class="day sun" style="left:922px;top:924px">16</span>
    <div class="week-rule" style="top:963px"></div>

    <span class="day" style="left:153px;top:1021px">17</span>
    <span class="day" style="left:274px;top:1021px">18</span>
    <span class="day" style="left:404px;top:1021px">19</span>
    <span class="day" style="left:534px;top:1021px">20</span>
    <span class="day" style="left:665px;top:1021px">21</span>
    <span class="day" style="left:792px;top:1021px">22</span>
    <span class="day sun" style="left:922px;top:1021px">23</span>
    <div class="week-rule" style="top:1062px"></div>

    <span class="day" style="left:153px;top:1116px">24</span>
    <span class="day" style="left:274px;top:1116px">25</span>
    <span class="day" style="left:404px;top:1116px">26</span>
    <span class="day" style="left:534px;top:1116px">27</span>
    <span class="day" style="left:665px;top:1116px">28</span>
    <span class="day" style="left:792px;top:1116px">29</span>
    <span class="day sun" style="left:922px;top:1116px">30</span>
    <div class="week-rule" style="top:1154px"></div>
  </div>

  <span class="site-url">www.spinefsw.example.org</span>
</div>
</body>
</html>
```